Restaurant Facility Equipment & Store Maintenance/

I need a flyer showing commercial/industrial kitchen equipment photos we work on Hot Equipment & Cold Equipment and offer many services. see attached highlights

```html
<!DOCTYPE html>
<html lang="en">
<head>
<meta charset="utf-8">
<title>Restaurant Facility Maintenance Flyer</title>
<link href="https://fonts.googleapis.com/css2?family=Open+Sans:wght@700;800&family=Roboto:wght@400;500&family=Roboto+Condensed:wght@700&display=swap" rel="stylesheet">
<style>
  :root {
    --backdrop: #c4bfb9;
    --navy: #0c2150;
    --royal: #1d4b96;
    --accent: #1f4e9c;
    --ink: #222222;
    --panel-grey: #f2f2f2;
    --panel-blue: #cfe2fb;
    --divider: #5a6d96;
    --white: #ffffff;
  }
  * { margin: 0; padding: 0; box-sizing: border-box; }
  html, body { width: 1200px; height: 2784px; overflow: hidden; background: var(--backdrop); }

  .flyer {
    position: absolute; left: 120px; top: 817px; width: 960px; height: 1150px;
    background: var(--white); overflow: hidden;
    font-family: "Roboto", Arial, sans-serif; color: var(--ink);
  }

  .hero-photo {
    position: absolute; left: 0; top: 0; width: 960px; height: 350px;
    background:
      linear-gradient(180deg, rgba(255,255,255,.85) 0%, rgba(255,255,255,0) 28%, rgba(60,66,74,.18) 70%, rgba(255,255,255,.25) 100%),
      linear-gradient(90deg, #b9c0c7 0%, #dfe3e6 14%, #8e979f 30%, #c7ccd1 44%, #6f767d 56%, #d9dde1 68%, #9aa2aa 82%, #eceff1 100%);
  }

  .headline-banner {
    position: absolute; left: 73px; top: 260px; width: 724px; height: 195px;
    background: var(--navy); color: var(--white); text-align: center;
    font-family: "Open Sans", Arial, sans-serif; font-weight: 800;
    box-shadow: 0 4px 10px rgba(0,0,0,.25);
  }
  .headline-banner .line { position: absolute; left: 0; width: 100%; white-space: nowrap; }
  .headline-banner .big { font-size: 48px; line-height: 56px; }
  .headline-banner .big.first { top: 18px; }
  .headline-banner .big.second { top: 75px; }
  .headline-banner .sub { top: 133px; font-size: 33px; line-height: 42px; font-weight: 700; }

  .intro {
    position: absolute; left: 0; top: 480px; width: 960px;
    font-size: 14.5px; line-height: 16px; text-align: center; white-space: nowrap;
  }

  .section-rule { position: absolute; top: 585px; height: 4px; background: var(--accent); }
  .section-rule.left { left: 0; width: 211px; }
  .section-rule.right { left: 595px; width: 365px; }
  .section-icon { position: absolute; left: 251px; top: 564px; width: 46px; height: 46px; }
  .section-title {
    position: absolute; left: 320px; top: 564px;
    font-family: "Roboto Condensed", Arial, sans-serif; font-weight: 700;
    font-size: 38px; line-height: 44px; color: var(--accent); white-space: nowrap;
  }

  .panel { position: absolute; }
  .panel.basics { left: 0; top: 638px; width: 435px; height: 418px; background: var(--panel-grey); }
  .panel.extras { left: 435px; top: 644px; width: 525px; height: 412px; background: var(--panel-blue); }

  .service { position: absolute; font-size: 14px; line-height: 16px; white-space: nowrap; }
  .service svg { position: absolute; left: -30px; top: 0; width: 15px; height: 15px; }
  .basics .service { left: 141px; }
  .extras .service { left: 82px; }
  .extras .service svg { left: -24px; }

  .phone-tab {
    position: absolute; left: 0; top: 992px; width: 301px; height: 64px;
    background: var(--royal); color: var(--white);
    font-weight: 500; font-size: 28px; white-space: nowrap;
  }
  .phone-tab svg { position: absolute; left: 23px; top: 10px; width: 44px; height: 44px; }
  .phone-tab span { position: absolute; left: 81px; top: 15px; line-height: 34px; }

  .footer {
    position: absolute; left: 0; top: 1056px; width: 960px; height: 94px;
    background: var(--navy); color: var(--white); font-size: 14.5px; line-height: 17px;
  }
  .footer .item { position: absolute; white-space: nowrap; }
  .footer .item svg { position: absolute; left: -19px; top: 2px; width: 12px; height: 12px; }
  .footer .address { left: 63px; top: 31px; }
  .footer .address svg { left: -16px; }
  .footer .email { left: 417px; top: 32px; }
  .footer .web { left: 662px; top: 32px; }
  .footer .divider { position: absolute; top: 27px; width: 1px; height: 30px; background: var(--divider); }
</style>
</head>
<body>
<div class="flyer">
  <div class="hero-photo" role="img" aria-label="Photo of a stainless steel commercial kitchen with gas ranges, fryers and a combi oven"></div>

  <div class="headline-banner">
    <div class="line big first">WE HANDLE</div>
    <div class="line big second">EVERYTHING FROM</div>
    <div class="line sub">THE FRONT DOOR TO THE BACK DOOR</div>
  </div>

  <p class="intro">Installation, Rebuilds, OSHA Inspection, and Preventive Maintenance Services for Denver Metro and Surrounding Areas.We<br>offer hot and cold equipment repair, cleaning, maintenance, handyman work, drywall, painting, door closers, floors, and<br>ceiling tiles. For any need in your restaurant, call us and we will send a skilled technician to manage all your commercial<br>andindustrial facility requirements.</p>

  <div class="section-rule left"></div>
  <div class="section-rule right"></div>
  <svg class="section-icon" viewBox="0 0 46 46" aria-hidden="true">
    <circle cx="23" cy="23" r="22" fill="var(--accent)"/>
    <circle cx="23" cy="23" r="18" fill="none" stroke="#fff" stroke-width="1.4"/>
    <circle cx="23" cy="23" r="9" fill="none" stroke="#fff" stroke-width="2" stroke-dasharray="3.5 2"/>
    <circle cx="23" cy="23" r="3.5" fill="none" stroke="#fff" stroke-width="1.8"/>
  </svg>
  <div class="section-title">OUR SERVICES</div>

  <svg width="0" height="0" style="position:absolute">
    <defs>
      <symbol id="tick" viewBox="0 0 16 16">
        <rect x="1" y="2" width="12" height="12" fill="none" stroke="var(--accent)" stroke-width="1.6"/>
        <path d="M4 8 L7 11 L15 2" fill="none" stroke="var(--accent)" stroke-width="2"/>
      </symbol>
    </defs>
  </svg>

  <div class="panel basics">
    <div class="service" style="top:50px"><svg><use href="#tick"/></svg>KESA Certified Technicians</div>
    <div class="service" style="top:88px"><svg><use href="#tick"/></svg>Round-the-clock emergency services</div>
    <div class="service" style="top:130px"><svg><use href="#tick"/></svg>Customers who subscribe to preventive<br>maintenance services receive a<br>reduced rate on hourly labor charges.</div>
    <div class="service" style="top:186px"><svg><use href="#tick"/></svg>Original equipment manufacturer<br>(OEM) parts</div>
    <div class="service" style="top:236px"><svg><use href="#tick"/></svg>30-day warranty on all OEM parts installed</div>
    <div class="service" style="top:272px"><svg><use href="#tick"/></svg>Equipment Cleaning &amp; Rebuilds</div>
    <div class="service" style="top:305px"><svg><use href="#tick"/></svg>Hot &amp; Cold Equipment</div>
  </div>

  <div class="panel extras">
    <div class="service" style="top:44px"><svg><use href="#tick"/></svg>Used equipment available for purchase or rental</div>
    <div class="service" style="top:78px"><svg><use href="#tick"/></svg>Specialized Programs for Preventive&nbsp; Maintenance<br>of Equipment</div>
    <div class="service" style="top:117px"><svg><use href="#tick"/></svg>Comprehensive licensed electrical contractor services<br>for both interior and exterior projects, including<br>lighting system upgrades.</div>
    <div class="service" style="top:180px"><svg><use href="#tick"/></svg>Repair or replace restaurant furniture</div>
    <div class="service" style="top:223px"><svg><use href="#tick"/></svg>Building Graffiti Removal Services</div>
    <div class="service" style="top:258px"><svg><use href="#tick"/></svg>Installation and Repair of Restaurant Equipment</div>
    <div class="service" style="top:293px"><svg><use href="#tick"/></svg>Food Service Trucks</div>
    <div class="service" style="top:326px"><svg><use href="#tick"/></svg>We repair floors, walls, counters, décor, signage,<br>parking lots, dumpsters, and more. If you have it,<br>we probably fix it.</div>
  </div>

  <div class="phone-tab">
    <svg viewBox="0 0 46 46" aria-hidden="true">
      <circle cx="23" cy="23" r="23" fill="#fff"/>
      <path d="M15 12 L19 12 L21 18 L18 20 C19.5 24 22 26.5 26 28 L28 25 L34 27 L34 31 C34 33 32 34 30 34 C21 33 13 25 12 16 C12 14 13 12 15 12 Z" fill="var(--royal)"/>
    </svg>
    <span>(303) 555-0187</span>
  </div>

  <div class="footer">
    <div class="item address">
      <svg viewBox="0 0 13 13" aria-hidden="true"><path d="M6.5 0 C3.5 0 2 2 2 4.3 C2 7 6.5 13 6.5 13 C6.5 13 11 7 11 4.3 C11 2 9.5 0 6.5 0 Z" fill="#fff"/><circle cx="6.5" cy="4.5" r="1.6" fill="var(--navy)"/></svg>
      <span>4820 Brighton Blvd, Unit 12,<br>Denver, CO 80216</span>
    </div>
    <div class="divider" style="left:358px"></div>
    <div class="item email">
      <svg viewBox="0 0 13 13" aria-hidden="true"><rect x="0" y="2" width="13" height="9" fill="#fff"/><path d="M0 2 L6.5 7 L13 2" fill="none" stroke="var(--navy)" stroke-width="1.2"/></svg>
      <span>help@frontbackfacility.com</span>
    </div>
    <div class="divider" style="left:613px"></div>
    <div class="item web">
      <svg viewBox="0 0 13 13" aria-hidden="true"><circle cx="6.5" cy="6.5" r="5.8" fill="none" stroke="#fff" stroke-width="1.3"/><ellipse cx="6.5" cy="6.5" rx="2.5" ry="5.8" fill="none" stroke="#fff" stroke-width="1.1"/><path d="M0.7 6.5 H12.3" stroke="#fff" stroke-width="1.1"/></svg>
      <span>www.frontbackfacility.com</span>
    </div>
  </div>
</div>
</body>
</html>
```